real estate managers brochure A5

Real estate services brochure (owners corporation management)

Content has been uploaded in MS word documents and we reserve the right to refine the text in one revision.

Visit out site http://www.marrowfen.com.au/body-corporate-managers/ and review the pages in the 'owners corporation' menu in our website - the brochure is for these services we provide.

We want to showcase a variety of 'trophy' buildings/unit/apartment/factory developments that we manage - I've uploaded these 'case studies' and high res images for each.

Some General services photos to be provided by you.

The brochure is given out to potential owners who we wish to be clients.

We are going to print a few dozen of these in hard copy so will need artwork in nigh resolution pdf format and a web resolution version for emailing potential clients.

Target Market(s)

Unit owners, apartment owners and commercial factory owners

Industry/Entity Type

Property Management

Font styles to use
Serif
Sans Serif

Requirements
Must have
• A modern design that looks like it could be just as home on a website or facebook post
• Have a flair of retro design and/or vintage graphics
• 3 full pages of example properties we manage property. see example properties in the case studies. I have uploaded high res images for the full page images and some brief text for these pages
Should not have
• Must not look like a typical real estate agents brochure (smiling agents, happy home owners)
• Images of people who do not look australian (ie afro american, asian) as this is not our target market. We typically have anglo australian or eruopean looking clients
• We are a young company who pride ourselves on. Efficient services and high tech management systems for the properties we manage

```html
<!DOCTYPE html>
<html lang="en">
<head>
<meta charset="utf-8">
<title>Management services – Marrowfen</title>
<link href="https://fonts.googleapis.com/css2?family=Open+Sans:wght@300;400;600;700&display=swap" rel="stylesheet">
<style>
  :root {
    --header-blue: #2f52a6;
    --header-blue-light: #3c61b8;
    --accent: #1f9ad6;
    --text: #6b6b6b;
    --bullet: #9a9a9a;
    --page: #ffffff;
  }
  * { box-sizing: border-box; margin: 0; padding: 0; }
  html, body { width: 943px; height: 1200px; overflow: hidden; background: var(--page); }
  body { font-family: "Open Sans", Arial, sans-serif; color: var(--text); }
  .page { width: 943px; height: 1200px; position: relative; overflow: hidden; }
  .page-header {
    height: 110px;
    background: linear-gradient(180deg, var(--header-blue-light), var(--header-blue));
    display: flex; align-items: center; justify-content: center;
  }
  .page-title { color: #fff; font-weight: 300; font-size: 56px; letter-spacing: 0.5px; line-height: 1; }
  .content { padding: 14px 90px 0 102px; }
  .intro { color: var(--accent); font-size: 20px; line-height: 26px; max-width: 720px; }
  .service-group h2 {
    color: var(--accent); font-size: 22px; font-weight: 700; line-height: 30px;
    margin: 24px 0 18px;
  }
  .service-list { list-style: none; }
  .service-list li {
    position: relative; padding-left: 49px;
    font-size: 19.5px; line-height: 26px; font-weight: 400;
  }
  .service-list li::before {
    content: ""; position: absolute; left: 10px; top: 11px;
    width: 5px; height: 5px; border-radius: 50%; background: var(--bullet);
  }
</style>
</head>
<body>
<div class="page">
  <header class="page-header">
    <h1 class="page-title">Management services</h1>
  </header>
  <main class="content">
    <p class="intro">MARROWFEN have developed a highly efficient management service with documented procedures and quality control.</p>

    <section class="service-group">
      <h2>Communication &amp; Customer Service</h2>
      <ul class="service-list">
        <li>Facilitate communication between owners, the Committee and residents</li>
        <li>Acknowledge the receipt of and respond to all correspondence promptly</li>
        <li>Maintain accurate records of all business conducted on your behalf</li>
        <li>Prepare and distribute all meeting notices, agendas and supporting documents</li>
        <li>Distribute minutes of Owners Corporation meetings</li>
      </ul>
    </section>

    <section class="service-group">
      <h2>Management</h2>
      <ul class="service-list">
        <li>Invoice statutory fee notices to Lot owners</li>
        <li>Ensure arrears and debts are efficiently managed</li>
        <li>Pay invoices and accounts as authorised</li>
        <li>Arrange and maintain insurance policies and valuations</li>
        <li>Arrange safety audits and building reports as required</li>
        <li>General asset management, arrange and coordinate contractors</li>
        <li>Report to the committee and members at your Annual General Meeting</li>
      </ul>
    </section>

    <section class="service-group">
      <h2>Financial</h2>
      <ul class="service-list">
        <li>Maintain the Owners Corporation bank accounts, (daily reconciliation)</li>
        <li>Receipt and bank all levies</li>
        <li>Manage and remit tax and other duties</li>
        <li>Provide financial statements and reports to your Committee as required</li>
        <li>Prepare an annual budget for admin. and maintenance funds</li>
      </ul>
    </section>

    <section class="service-group">
      <h2>Services</h2>
      <ul class="service-list">
        <li>Conduct the annual general meeting</li>
        <li>Support the operation of the Owners Corporation Committee</li>
        <li>Guide you to comply with the Owners Corporations Act, Regulations and your Rules</li>
        <li>Maintain the owners corporation register</li>
        <li>Implement and operate a grievance procedure</li>
        <li>Provide prompt attention to authorised requests</li>
        <li>Custody and use of/affixing common seal</li>
      </ul>
    </section>
  </main>
</div>
</body>
</html>
```